Brochure about Gun Trusts

Cover Page: Image of a firearm collection or a lockbox with the title]
Headline: Protect Your Firearms Collection with a Gun Trust
Subheading: Ensure Your Legacy Remains Private and Your Wishes Are Respected
[Page 1: What is a Gun Trust?]
Definition: A legally recognized trust that allows you to collect, own, and transfer firearms, including those restricted by the KRC.
Quote: "A gun trust is a revocable trust created to hold ownership of a firearm..." - BQM
[Page 2: Benefits of a Gun Trust]
Avoid Probate: Keep your firearms out of the public probate process, maintaining your privacy.
Multi-Generational Ownership: Easily transfer ownership to beneficiaries without the need for a court proceeding.
Shared Responsibility: Allow others to legally possess and use the firearms held in the trust.
[Page 3: The Risks of Not Having a Gun Trust]
Inheritance Issues: Firearms may not be transferred as intended, potentially leading to legal complications.
Probate and Public Disclosure: Your firearms collection becomes a public record.
[Page 4: How to Set Up a Gun Trust]
Consult with an Attorney: A firearms trust attorney will create a trust that complies with all federal and state laws.
Assign a Trustee: Choose a trustee to manage the trust if you become incapacitated or pass away.
Transfer Ownership: Assign your firearms to the trust.
[Back Cover: Call to Action]
Headline: Protect Your Firearms Legacy
Contact Information: Address, Phone Number, Email, Website
Offer: Free Consultation to discuss your options

```html
<!DOCTYPE html>
<html lang="en">
<head>
<meta charset="utf-8">
<title>Gun Trust Brochure</title>
<link href="https://fonts.googleapis.com/css2?family=Oswald:wght@500;700&family=Poppins:wght@400;500;600;700&display=swap" rel="stylesheet">
<style>
:root{
  --stage:#9a9a9a;
  --red:#a60d12;
  --red-deep:#840a0d;
  --gold:#f6a81c;
  --ink:#1b1b1b;
  --ink-soft:#2d2d2d;
  --white:#ffffff;
  --rule:#d9a0a0;
}
*{box-sizing:border-box;margin:0;padding:0}
html,body{width:1200px;height:2400px;overflow:hidden;background:var(--stage)}
body{position:relative;font-family:"Poppins",sans-serif;color:var(--ink)}
.page{position:absolute;width:484px;height:626px;overflow:hidden;background:var(--white);box-shadow:0 6px 14px rgba(0,0,0,.35)}
.col-left{left:81px}.col-right{left:641px}
.row-1{top:173px}.row-2{top:887px}.row-3{top:1601px}
.photo{position:absolute}
.display{font-family:"Oswald",sans-serif;font-weight:700;text-transform:uppercase;line-height:.98;letter-spacing:.5px}
.gold{color:var(--gold)}
.footer-url{position:absolute;font-size:10.5px;letter-spacing:2px;color:var(--ink)}
.footer-rule{position:absolute;height:1px;background:#777}
.page-num{position:absolute;font-size:7px;font-weight:700;color:var(--ink)}

/* cover */
.cover{background:linear-gradient(180deg,#b0141a,#8f0b10)}
.cover-title{position:absolute;top:42px;left:0;width:100%;text-align:center;color:var(--white)}
.cover-title .lead{display:block;font-size:33px;font-weight:500;line-height:1}
.cover-title .main{display:block;font-family:"Oswald",sans-serif;font-weight:700;font-size:50px;color:var(--gold);line-height:1.02;text-transform:uppercase}
.cover-title .tail{display:block;font-size:33px;font-weight:400;line-height:1}
.cover-sub{position:absolute;top:508px;width:100%;text-align:center;color:var(--white);font-size:18px;line-height:1.3;font-weight:500}
.cover-url{position:absolute;top:574px;width:100%;text-align:center;color:var(--white);font-size:14px;letter-spacing:3px}
.cover-url b{color:var(--gold);font-weight:700}

/* what is */
.what-head{position:absolute;top:0;left:0;width:100%;height:180px;background:#0f1418}
.what-title{position:absolute;top:34px;left:26px;font-size:66px;color:var(--gold)}
.what-kicker{position:absolute;top:215px;left:34px;color:var(--red);font-weight:700;font-size:21px;letter-spacing:3px}
.what-lead{position:absolute;top:240px;left:34px;font-size:20px;line-height:1.3;font-weight:500}
.verb-list{position:absolute;top:312px;left:26px;list-style:none}
.verb-list li{display:flex;align-items:center;height:44px;font-size:15px;letter-spacing:.5px}
.verb-list li span{display:inline-block;width:120px;border-bottom:1px dotted #b66;padding:6px 0 8px}
.hex{width:40px;height:40px;margin-right:20px;flex:none}
.agency-box{position:absolute;top:472px;left:26px;width:240px;height:66px;border:1px solid var(--red);border-radius:8px;display:flex;align-items:center}
.agency-name{font-size:30px;font-weight:700;color:var(--red);width:92px;text-align:center}
.agency-box p{font-size:12px;font-weight:600;line-height:1.3}
.quote-box{position:absolute;top:222px;left:292px;width:166px;height:194px;background:var(--red);border-radius:8px;color:var(--white);padding:30px 14px 0 16px;font-size:15.5px;font-weight:700;line-height:1.25}
.quote-box .by{margin-top:24px;font-size:15px}
.quote-mark{position:absolute;font-family:"Oswald",sans-serif;font-weight:700;font-size:72px;color:var(--red);line-height:1}

/* split pages */
.split-col{position:absolute;top:0;left:0;width:198px;height:100%}
.split-title{position:absolute;white-space:nowrap}
.split-title span{display:block}
.split-title .dark{color:#2a2522}
.split-rule{position:absolute;height:2px;background:linear-gradient(90deg,var(--red),rgba(166,13,18,0))}
.step{position:absolute;left:215px;width:255px;display:flex}
.step .badge{width:50px;height:50px;flex:none;margin-right:26px}
.step h3{font-size:12.5px;font-weight:700;line-height:1.25}
.step p{font-size:12.5px;line-height:1.25}
.step.accent h3{color:var(--gold)}
.step-rule{position:absolute;left:292px;width:165px;border-top:1px dotted #c88}

/* risks */
.risk-top{position:absolute;top:0;left:0;width:100%;height:396px;background:#050505}
.risk-title{position:absolute;top:34px;width:100%;text-align:center;font-size:52px;color:var(--white)}
.risk-bar{position:absolute;left:24px;width:432px;height:60px;border-radius:8px;padding:8px 0 0 96px;color:var(--white);font-size:13px;line-height:1.25}
.risk-bar b{display:block;color:var(--gold);font-size:13px}
.risk-hex{position:absolute;left:-2px;top:2px;width:60px;height:56px}

/* back cover */
.back{background:var(--red)}
.back-band{position:absolute;top:300px;left:0;width:100%;height:326px;background:linear-gradient(180deg,#a70e13,#8f0b10);text-align:center;color:var(--white)}
.back-band .lead{font-size:21px;font-weight:500;margin-top:16px;line-height:1}
.back-band .main{font-family:"Oswald",sans-serif;font-weight:700;font-size:32px;color:var(--gold);line-height:1.1}
.back-band .tail{font-size:21px;line-height:1}
.offer{font-size:12.5px;margin-top:12px}
.offer b{font-weight:700}
.contact-icons{display:flex;justify-content:center;align-items:center;margin-top:18px}
.contact-icons svg{width:24px;height:24px}
.contact-icons .link{width:16px;height:1px;background:var(--gold)}
.back-band .phone{font-weight:700;font-size:13px;margin-top:16px}
.back-band .addr{font-size:13px;line-height:1.3;margin-top:8px}
.back-band .mail{font-size:13px;margin-top:10px}
.back-band .site{font-size:15px;letter-spacing:3px;margin-top:10px}
.back-band .site b{color:var(--gold)}
</style>
</head>
<body>

<section class="page cover col-left row-1">
  <h1 class="cover-title">
    <span class="lead">PROTECT YOUR</span>
    <span class="main">Firearms Collection</span>
    <span class="tail">WITH A GUN TRUST</span>
  </h1>
  <div class="photo" style="top:171px;left:0;width:484px;height:318px;background:linear-gradient(135deg,#2a2a2a,#111 60%,#262018)" role="img" aria-label="Firearm collection: rifle, pistol, revolver and a box of ammunition on a dark surface"></div>
  <p class="cover-sub">Ensure Your Legacy Remains Private &amp;<br><span class="gold">Your Wishes Are Respected</span></p>
  <p class="cover-url">www.<b>armslegacy</b>.com</p>
</section>

<section class="page col-right row-1">
  <div class="what-head"></div>
  <div class="photo" style="top:0;left:270px;width:214px;height:215px;background:radial-gradient(circle at 50% 50%,#4a5358,#1a2226 70%,#0f1418)" role="img" aria-label="Semi-automatic pistol with scattered cartridges"></div>
  <h2 class="display what-title">What is a<br>Gun Trust?</h2>
  <p class="what-kicker">A LEGALLY</p>
  <p class="what-lead">Recognized trust<br>that allows you to</p>
  <ul class="verb-list">
    <li><svg class="hex" viewBox="0 0 40 40"><polygon points="20,2 36,11 36,29 20,38 4,29 4,11" fill="none" stroke="#a60d12" stroke-width="2.5"/><rect x="13" y="15" width="14" height="5" fill="none" stroke="#a60d12" stroke-width="1.5"/><rect x="14" y="20" width="4" height="7" fill="none" stroke="#a60d12" stroke-width="1.5"/></svg><span>COLLECT</span></li>
    <li><svg class="hex" viewBox="0 0 40 40"><polygon points="20,2 36,11 36,29 20,38 4,29 4,11" fill="none" stroke="#a60d12" stroke-width="2.5"/><circle cx="20" cy="15" r="4" fill="none" stroke="#a60d12" stroke-width="1.5"/><path d="M12 28c1-5 4-7 8-7s7 2 8 7" fill="none" stroke="#a60d12" stroke-width="1.5"/></svg><span>OWN</span></li>
    <li><svg class="hex" viewBox="0 0 40 40"><polygon points="20,2 36,11 36,29 20,38 4,29 4,11" fill="none" stroke="#a60d12" stroke-width="2.5"/><path d="M12 17h14l-3-3M28 23H14l3 3" fill="none" stroke="#a60d12" stroke-width="1.5"/></svg><span>TRANSFER</span></li>
  </ul>
  <div class="agency-box">
    <span class="agency-name">KRC</span>
    <p>Including those<br>restricted by the KRC.</p>
  </div>
  <span class="quote-mark" style="top:198px;left:294px">“</span>
  <blockquote class="quote-box">A gun trust is a revocable trust created to hold ownership of a firearm...<p class="by">- BQM</p></blockquote>
  <span class="quote-mark" style="top:384px;left:424px">”</span>
  <div class="photo" style="top:437px;left:298px;width:160px;height:104px;border:2px solid var(--red);background:linear-gradient(135deg,#6e6a62,#3c3a36)" role="img" aria-label="Instructor guiding a student holding a handgun outdoors"></div>
  <p class="footer-url" style="top:586px;left:29px">www.armslegacy.com</p>
  <div class="footer-rule" style="top:596px;left:163px;width:295px"></div>
  <span class="page-num" style="top:588px;left:454px">1</span>
</section>

<section class="page col-left row-2">
  <div class="split-col" role="img" aria-label="Gavel, law books and handcuffs on a desk" style="background:linear-gradient(180deg,#c98a2e 0%,#5d4020 35%,#3b3b3b 65%,#8e0b10 100%)"></div>
  <h2 class="display split-title" style="top:38px;left:215px"><span class="dark" style="font-size:42px">Benefits of a</span><span class="gold" style="font-size:58px">Gun Trust</span></h2>
  <div class="split-rule" style="top:155px;left:215px;width:250px"></div>
  <div class="step" style="top:196px">
    <svg class="badge" viewBox="0 0 50 50"><circle cx="24" cy="25" r="21" fill="#fff" stroke="#a60d12" stroke-width="3"/><path d="M45 25l5 0" stroke="#a60d12" stroke-width="3"/><rect x="17" y="16" width="14" height="18" fill="none" stroke="#333" stroke-width="1.4"/><path d="M20 21h8M20 25h8M20 29h6" stroke="#333" stroke-width="1.2"/></svg>
    <div><h3>Avoid Probate:</h3><p>Keep your firearms out of the public probate process, maintaining your privacy.</p></div>
  </div>
  <div class="step-rule" style="top:275px"></div>
  <div class="step" style="top:288px">
    <svg class="badge" viewBox="0 0 50 50"><circle cx="24" cy="25" r="21" fill="#fff" stroke="#f6a81c" stroke-width="3"/><path d="M45 25l5 0" stroke="#f6a81c" stroke-width="3"/><circle cx="24" cy="19" r="4" fill="none" stroke="#333" stroke-width="1.4"/><path d="M16 33c1-5 4-8 8-8s7 3 8 8z" fill="none" stroke="#333" stroke-width="1.4"/></svg>
    <div><h3>Multi-Generational<br>Ownership:</h3><p>Easily transfer ownership<br>to beneficiaries without<br>the need for a court<br>proceeding.</p></div>
  </div>
  <div class="step-rule" style="top:396px"></div>
  <div class="step" style="top:408px">
    <svg class="badge" viewBox="0 0 50 50"><circle cx="24" cy="25" r="21" fill="#fff" stroke="#a60d12" stroke-width="3"/><path d="M45 25l5 0" stroke="#a60d12" stroke-width="3"/><circle cx="19" cy="20" r="3.5" fill="none" stroke="#333" stroke-width="1.4"/><circle cx="29" cy="28" r="3.5" fill="none" stroke="#333" stroke-width="1.4"/><path d="M22 23l4 3" stroke="#333" stroke-width="1.2"/></svg>
    <div><h3>Shared<br>Responsibility:</h3><p>Allow others to<br>legally possess and<br>use the firearms held<br>in the trust.</p></div>
  </div>
  <p class="footer-url" style="top:586px;left:26px;color:#fff">www.armslegacy.com</p>
  <div class="footer-rule" style="top:596px;left:160px;width:296px"></div>
  <span class="page-num" style="top:588px;left:452px">2</span>
</section>

<section class="page col-right row-2">
  <div class="risk-top"></div>
  <div class="photo" style="top:150px;left:0;width:484px;height:246px;background:linear-gradient(180deg,#050505,#3a2a18 45%,#2a2a2a)" role="img" aria-label="Person handling a tactical rifle at a workbench"></div>
  <h2 class="display risk-title">The Risks of Not<br><span class="gold">Having a Gun Trust</span></h2>
  <div class="risk-bar" style="top:422px;background:var(--red)">
    <svg class="risk-hex" viewBox="0 0 60 56"><polygon points="30,3 55,15 55,41 30,53 5,41 5,15" fill="#fff" stroke="#a60d12" stroke-width="3"/><rect x="22" y="22" width="16" height="6" fill="none" stroke="#a60d12" stroke-width="1.6"/><rect x="23" y="28" width="5" height="8" fill="none" stroke="#a60d12" stroke-width="1.6"/></svg>
    <b>Inheritance Issues:</b>Firearms may not be transferred as intended, potentially leading to legal complications.
  </div>
  <div class="risk-bar" style="top:492px;background:#111;padding-top:12px">
    <svg class="risk-hex" viewBox="0 0 60 56"><polygon points="30,3 55,15 55,41 30,53 5,41 5,15" fill="#fff" stroke="#111" stroke-width="3"/><circle cx="30" cy="22" r="4" fill="none" stroke="#a60d12" stroke-width="1.6"/><path d="M22 36c1-5 4-8 8-8s7 3 8 8" fill="none" stroke="#a60d12" stroke-width="1.6"/></svg>
    <b>Probate and Public Disclosure:</b>Your firearms collection becomes a public record.
  </div>
  <p class="footer-url" style="top:586px;left:29px">www.armslegacy.com</p>
  <div class="footer-rule" style="top:596px;left:163px;width:295px"></div>
  <span class="page-num" style="top:588px;left:454px">3</span>
</section>

<section class="page col-left row-3">
  <div class="split-col" role="img" aria-label="Pistol with cartridges above a hand signing a contract agreement" style="width:190px;background:linear-gradient(180deg,#a60d12 0%,#8e0b10 45%,#5a2a30 70%,#2c2c34 100%)"></div>
  <h2 class="display split-title" style="top:22px;left:229px;font-size:52px;line-height:1.02"><span class="dark">How to</span><span class="dark">Set up a</span><span class="gold">Gun Trust</span></h2>
  <div class="split-rule" style="top:193px;left:229px;width:240px"></div>
  <div class="step" style="top:240px;left:208px">
    <svg class="badge" viewBox="0 0 50 50"><circle cx="24" cy="25" r="21" fill="#fff" stroke="#a60d12" stroke-width="3"/><path d="M45 25l5 0" stroke="#a60d12" stroke-width="3"/><circle cx="24" cy="19" r="4" fill="none" stroke="#333" stroke-width="1.4"/><path d="M16 33h16M18 33v-4h12v4" fill="none" stroke="#333" stroke-width="1.4"/></svg>
    <div><h3>Consult with an<br>Attorney:</h3><p>A firearms trust attorney<br>will create a trust that<br>complies with all federal<br>and state laws.</p></div>
  </div>
  <div class="step-rule" style="top:346px;left:285px"></div>
  <div class="step accent" style="top:360px;left:208px">
    <svg class="badge" viewBox="0 0 50 50"><circle cx="24" cy="25" r="21" fill="#fff" stroke="#f6a81c" stroke-width="3"/><path d="M45 25l5 0" stroke="#f6a81c" stroke-width="3"/><rect x="17" y="16" width="14" height="18" fill="none" stroke="#333" stroke-width="1.4"/><path d="M20 21h8M20 25h8M20 29h6" stroke="#333" stroke-width="1.2"/></svg>
    <div><h3>Assign a Trustee:</h3><p>Choose a trustee to manage the trust if you become incapacitated or pass away.</p></div>
  </div>
  <div class="step-rule" style="top:449px;left:285px"></div>
  <div class="step accent" style="top:469px;left:208px">
    <svg class="badge" viewBox="0 0 50 50"><circle cx="24" cy="25" r="21" fill="#fff" stroke="#a60d12" stroke-width="3"/><path d="M45 25l5 0" stroke="#a60d12" stroke-width="3"/><path d="M16 21h14l-3-3M32 29H18l3 3" fill="none" stroke="#333" stroke-width="1.4"/></svg>
    <div><h3>Transfer Ownership:</h3><p>Assign your firearms<br>to the trust.</p></div>
  </div>
  <p class="footer-url" style="top:590px;left:30px;color:#fff">www.armslegacy.com</p>
  <div class="footer-rule" style="top:600px;left:190px;width:268px"></div>
  <span class="page-num" style="top:592px;left:455px">4</span>
</section>

<section class="page back col-right row-3">
  <div class="photo" style="top:0;left:0;width:484px;height:310px;background:linear-gradient(135deg,#2f343a,#1b1f24 55%,#3a3e44)" role="img" aria-label="Handgun and magazine beside a tray of cartridges on dark fabric"></div>
  <div class="back-band">
    <p class="lead">PROTECT YOUR</p>
    <p class="main">FIREARMS COLLECTION</p>
    <p class="tail">WITH A GUN TRUST</p>
    <p class="offer"><b>FREE CONSULTATION</b> TO DISCUSS YOUR OPTIONS</p>
    <div class="contact-icons" aria-hidden="true">
      <svg viewBox="0 0 24 24"><circle cx="12" cy="12" r="11" fill="#f6a81c"/><path d="M8 6l2 0 1 3-1.5 1c.8 1.8 2 3 3.5 3.5L14 12l3 1v2c0 1-1 1.5-2 1.3C10.5 15.5 8.5 13 7.5 9 7.3 7 7.5 6 8 6z" fill="#222"/></svg>
      <span class="link"></span>
      <svg viewBox="0 0 24 24"><circle cx="12" cy="12" r="11" fill="#f6a81c"/><path d="M12 5a4 4 0 0 1 4 4c0 3-4 8-4 8s-4-5-4-8a4 4 0 0 1 4-4z" fill="#222"/><circle cx="12" cy="9" r="1.5" fill="#f6a81c"/></svg>
      <span class="link"></span>
      <svg viewBox="0 0 24 24"><circle cx="12" cy="12" r="11" fill="#f6a81c"/><rect x="6" y="8" width="12" height="8" fill="#222"/><path d="M6 8l6 5 6-5" fill="none" stroke="#f6a81c" stroke-width="1"/></svg>
      <span class="link"></span>
      <svg viewBox="0 0 24 24"><circle cx="12" cy="12" r="11" fill="#f6a81c"/><circle cx="12" cy="12" r="6" fill="none" stroke="#222" stroke-width="1.4"/><path d="M6 12h12M12 6c-3 3-3 9 0 12M12 6c3 3 3 9 0 12" fill="none" stroke="#222" stroke-width="1.2"/></svg>
    </div>
    <p class="phone">5550142876</p>
    <p class="addr">Lorem ipsum dolor sit amet,<br>consectetur adipiscing elit,</p>
    <p class="mail">info@armslegacy.com</p>
    <p class="site">www.<b>armslegacy</b>.com</p>
  </div>
</section>

</body>
</html>
```